Business Card Design

educational services
broker of essential services
So I love my The Velvet Kettle cards. I love the background.
I like the background on the copper valley card
I like a little part of each Meridel card
I want my card to stand out and be professional
I would also like somewhat of a brand
I do not want it to be specific to anything but the world and galaxy
I would like to be able to be used for everything, all encompassing
In spanish Cielo abierto, not sureother languages but i will do programs for other countries like China, Japan and Korea
Reason: It has been the first week of school and I have not been able to get the feedback I need.
Please change colors to Blue and GOld
Please add ~ over the n in Lorna
Please submit some vertical designs
Please include the world
Please make eagle a watermark
Make sure the Open Horizon doesnt have "preparatory school" under it
I am open to new designs and I will pay more after I chose a designer who seems to get all this stuff in my head!
Reason: Last minute designs were wonderful
Reason: I was out of town and not able to review the wonderful designs posted. I am narrowing the designs down now! I appreciate all the work done thus far.
Hello,
Thank you for all the designs. This is difficult. I have not been able to access them as I was able to last week so please be patient. If you also do web design please send me a message.
Again, thank you. I am down to just a few designs.
Sincerely,
Lorna Vickers Dunmore
I have been extremely busy, I should pick a design by the ned of this week. Thank you for your patience
Industry/Entity Type
Business
Contact Information for Business Card
Dr. Lorna Vickers Dunmore
www.ohacad.example
(555) 284-9306 US
lornajeanvickers@mailbox.example

```html
<!DOCTYPE html>
<html lang="en">
<head>
<meta charset="utf-8">
<title>Open Horizon – Business Cards</title>
<link href="https://fonts.googleapis.com/css2?family=Arimo:wght@400;700&family=Roboto+Condensed:wght@700&display=swap" rel="stylesheet">
<style>
  :root {
    --plum: #5e0a31;
    --plum-deep: #4d0727;
    --magenta: #b0126c;
    --magenta-light: #d0228a;
    --gold: #c9b21c;
    --paper: #f7f6f4;
    --ink-light: #ffffff;
    --stage: #ececec;
  }
  * { box-sizing: border-box; margin: 0; padding: 0; }
  html, body {
    width: 1200px; height: 977px; overflow: hidden;
    background: var(--stage);
  }
  .sheet {
    position: relative; width: 1200px; height: 977px;
    display: flex; align-items: center; justify-content: center; gap: 60px;
  }
  .card {
    position: relative; width: 500px; height: 286px;
    background: var(--plum); overflow: hidden;
    box-shadow: 0 6px 18px rgba(0,0,0,.18);
  }
  .card__band {
    position: absolute; left: 0; right: 0; top: 34px; height: 78px;
    display: flex; align-items: center; justify-content: flex-end;
    padding-right: 34px; gap: 12px;
  }
  .card--magenta .card__band {
    background: linear-gradient(90deg, var(--plum) 0%, var(--magenta) 35%, var(--magenta-light) 65%, var(--magenta) 100%);
  }
  .card--paper .card__band { background: var(--paper); }
  .brand__mark {
    width: 34px; height: 34px; border-radius: 50%;
    background: var(--plum-deep);
  }
  .card--paper .brand__mark { background: var(--plum); }
  .brand__name {
    font-family: "Arimo", Arial, sans-serif; font-weight: 700;
    font-size: 34px; letter-spacing: 1px; color: var(--gold);
    text-transform: uppercase; line-height: 1;
  }
  .card__details {
    position: absolute; left: 150px; top: 130px;
  }
  .holder {
    font-family: "Roboto Condensed", "Arial Narrow", sans-serif; font-weight: 700;
    font-size: 17px; color: var(--gold); margin-bottom: 10px;
  }
  .contact { list-style: none; }
  .contact__item {
    display: flex; align-items: center; gap: 10px;
    font-family: "Arimo", Arial, sans-serif; font-size: 15.5px;
    color: var(--ink-light); height: 27px;
  }
  .contact__icon { width: 15px; height: 15px; flex: none; }
</style>
</head>
<body>
<main class="sheet">

  <article class="card card--magenta">
    <div class="card__band">
      <span class="brand__mark"></span>
      <span class="brand__name">Open Horizon</span>
    </div>
    <div class="card__details">
      <p class="holder">Dr. Lorna Vickers Dunmore</p>
      <ul class="contact">
        <li class="contact__item">
          <svg class="contact__icon" viewBox="0 0 16 16"><circle cx="8" cy="8" r="8" fill="#fff"/><path d="M5.5 4.2l1.4 1.6-.8 1a5 5 0 0 0 2.9 2.9l1-.8 1.6 1.4-.9 1.3C8.2 11.5 4.5 7.8 4.3 5.1z" fill="#5e0a31"/></svg>
          (555) 284-9306 US
        </li>
        <li class="contact__item">
          <svg class="contact__icon" viewBox="0 0 16 16"><circle cx="8" cy="8" r="8" fill="#fff"/><rect x="4" y="5.2" width="8" height="5.6" fill="none" stroke="#5e0a31" stroke-width="1.1"/><path d="M4 5.4l4 3 4-3" fill="none" stroke="#5e0a31" stroke-width="1.1"/></svg>
          lornajeanvickers@mailbox.example
        </li>
        <li class="contact__item">
          <svg class="contact__icon" viewBox="0 0 16 16"><circle cx="8" cy="8" r="8" fill="#fff"/><circle cx="8" cy="8" r="4.3" fill="none" stroke="#5e0a31" stroke-width="1"/><ellipse cx="8" cy="8" rx="1.8" ry="4.3" fill="none" stroke="#5e0a31" stroke-width="1"/><path d="M3.7 8h8.6" stroke="#5e0a31" stroke-width="1"/></svg>
          www.ohacad.example
        </li>
      </ul>
    </div>
  </article>

  <article class="card card--paper">
    <div class="card__band">
      <span class="brand__mark"></span>
      <span class="brand__name">Open Horizon</span>
    </div>
    <div class="card__details">
      <p class="holder">Dr. Lorna Vickers Dunmore</p>
      <ul class="contact">
        <li class="contact__item">
          <svg class="contact__icon" viewBox="0 0 16 16"><circle cx="8" cy="8" r="8" fill="#fff"/><path d="M5.5 4.2l1.4 1.6-.8 1a5 5 0 0 0 2.9 2.9l1-.8 1.6 1.4-.9 1.3C8.2 11.5 4.5 7.8 4.3 5.1z" fill="#5e0a31"/></svg>
          (555) 284-9306 US
        </li>
        <li class="contact__item">
          <svg class="contact__icon" viewBox="0 0 16 16"><circle cx="8" cy="8" r="8" fill="#fff"/><rect x="4" y="5.2" width="8" height="5.6" fill="none" stroke="#5e0a31" stroke-width="1.1"/><path d="M4 5.4l4 3 4-3" fill="none" stroke="#5e0a31" stroke-width="1.1"/></svg>
          lornajeanvickers@mailbox.example
        </li>
        <li class="contact__item">
          <svg class="contact__icon" viewBox="0 0 16 16"><circle cx="8" cy="8" r="8" fill="#fff"/><circle cx="8" cy="8" r="4.3" fill="none" stroke="#5e0a31" stroke-width="1"/><ellipse cx="8" cy="8" rx="1.8" ry="4.3" fill="none" stroke="#5e0a31" stroke-width="1"/><path d="M3.7 8h8.6" stroke="#5e0a31" stroke-width="1"/></svg>
          www.ohacad.example
        </li>
      </ul>
    </div>
  </article>

</main>
</body>
</html>
```